Tech business card design

We need an amazing business card design for our new business 'Pexla' a marketing tech startup based in Sydney, Australia. We provide an online marketplace for businesses to search and buy advertising media, connect with service providers and learn more about marketing. We wish to communicate 'cool tech', reliability and professionalism and design based around our logo.

Target Market(s)

Business Owners

Contact Information for Business Card

Name
Position
Email Address
Website
Phone Number

Font styles to use
Other font styles liked:
• Avenir & Avenir Next

Colors

Designer to choose colors to be used in the design.

```html
<!DOCTYPE html>
<html lang="en">
<head>
<meta charset="UTF-8">
<title>Pexla Business Card</title>
<link rel="stylesheet" href="https://fonts.googleapis.com/css2?family=Mulish:wght@400;600;800;900&display=swap">
<style>
  :root {
    --backdrop: #3a3b3e;
    --navy: #0b1a45;
    --navy-soft: #1a2a5c;
    --paper: #ffffff;
    --ink: #0e1838;
    --ink-muted: #555a66;
    --logo-white: #f2f3f6;
  }
  * { box-sizing: border-box; margin: 0; padding: 0; }
  html, body {
    width: 1200px;
    height: 864px;
    overflow: hidden;
    background: var(--backdrop);
    font-family: "Mulish", sans-serif;
  }
  .stage {
    position: relative;
    width: 1200px;
    height: 864px;
  }
  .card {
    position: absolute;
    width: 600px;
    height: 340px;
    overflow: hidden;
  }
  .card--front {
    left: 230px;
    top: 60px;
    background: var(--navy);
  }
  .card--back {
    left: 370px;
    top: 450px;
    background: var(--paper);
  }
  .card__arc {
    position: absolute;
    inset: 0;
    width: 100%;
    height: 100%;
  }
  .wordmark {
    position: absolute;
    font-weight: 900;
    font-size: 76px;
    letter-spacing: -1px;
    line-height: 1;
  }
  .card--front .wordmark {
    left: 50%;
    top: 118px;
    transform: translateX(-50%);
    color: var(--logo-white);
  }
  .card--back .wordmark {
    left: 50%;
    top: 128px;
    transform: translateX(-50%);
    color: var(--navy);
  }
  .holder {
    position: absolute;
    right: 26px;
    top: 24px;
    text-align: right;
  }
  .holder__name {
    font-weight: 800;
    font-size: 17px;
    letter-spacing: 1px;
    color: var(--ink);
  }
  .holder__role {
    font-weight: 400;
    font-size: 15px;
    color: var(--ink-muted);
    margin-top: 2px;
  }
  .contact {
    position: absolute;
    left: 28px;
    bottom: 66px;
    color: var(--ink);
  }
  .contact__phone {
    font-weight: 600;
    font-size: 17px;
  }
  .contact__email {
    font-size: 15px;
    margin-top: 4px;
  }
  .website {
    position: absolute;
    right: 28px;
    bottom: 24px;
    font-size: 15px;
    color: var(--ink);
  }
</style>
</head>
<body>
  <main class="stage">
    <section class="card card--front" aria-label="Card front">
      <svg class="card__arc" viewBox="0 0 600 340" preserveAspectRatio="none" aria-hidden="true">
        <defs>
          <linearGradient id="arcGlow" x1="0" y1="0" x2="0" y2="1">
            <stop offset="0" stop-color="#2a3a70" stop-opacity="0.75"/>
            <stop offset="1" stop-color="#0b1a45" stop-opacity="0"/>
          </linearGradient>
        </defs>
        <path d="M0 250 Q300 120 600 250 L600 340 L0 340 Z" fill="url(#arcGlow)"/>
      </svg>
      <div class="wordmark">pexla</div>
    </section>

    <section class="card card--back" aria-label="Card back">
      <div class="holder">
        <p class="holder__name">DANIEL MARSH</p>
        <p class="holder__role">Managing Director</p>
      </div>
      <div class="wordmark">pexla</div>
      <div class="contact">
        <p class="contact__phone">000-987-6543</p>
        <p class="contact__email">info@pexlamail.com</p>
      </div>
      <p class="website">www.pexla.com</p>
    </section>
  </main>
</body>
</html>
```